Cleaning service website design

We need a new nice web design(logo will be the same) for a new cleaning service Company:

Informations about Company and logo you can take from flyers in attachments.

This is a cleaning service Company which have simple rules and we would like to show that(in checklist form) on website:

- What we do and that we're Cleaning Green

- Why us?

- How much(our pricing is simple)

Also we would like to communicate with clients by some nice/big pictures on website and the most important thing is our phone number and short/fast Brimtallow.

Also there should be some space for description about our Company.

Generally all information on main page can be short: about us, about service(what we do), last reviews, tips (for example: Tip of the week) and other can be some introduction to subpage where will be more information.

There will be few subpages like: About us, About our service, Photos(Before and after), Reviews , Tips, FAQ, Contact, Looking for a Job? - most of them will be just text so you can project just one example.

```html
<!DOCTYPE html>
<html lang="en">
<head>
<meta charset="utf-8">
<title>Tidy Nest – House Cleaning</title>
<link href="https://fonts.googleapis.com/css2?family=Source+Sans+3:wght@300;400;600;700&display=swap" rel="stylesheet">
<style>
  :root{
    --nav-text:#3d3d3d;
    --nav-active:#7ec256;
    --header-bg:#ffffff;
    --header-shade:#d9d9d9;
    --brand-blue:#1a5fa8;
    --brand-green:#7bbf5e;
    --price-red:#d8161b;
    --white:#ffffff;
    --btn-top:#ffce1a;
    --btn-bottom:#ff8a00;
    --leaf:#6fb52c;
  }
  *{margin:0;padding:0;box-sizing:border-box}
  html,body{width:1200px;height:637px;overflow:hidden;background:#fff}
  body{font-family:"Source Sans 3",sans-serif;position:relative}

  .site-header{position:absolute;left:0;top:0;width:1200px;height:134px;background:var(--header-bg);border-bottom:6px solid var(--header-shade);z-index:2}
  .brand{position:absolute;left:149px;top:15px;width:172px;height:99px;display:flex;align-items:center;gap:10px}
  .brand-mark{width:26px;height:26px;border-radius:50%;background:var(--brand-green);flex:none}
  .brand-name{font-size:30px;font-weight:600;color:var(--brand-blue);white-space:nowrap}

  .call-box{position:absolute;right:150px;top:13px;text-align:right;color:var(--nav-text)}
  .call-line{font-size:15px;font-weight:400}
  .call-line strong{font-weight:700}
  .call-phone{display:flex;align-items:center;justify-content:flex-end;gap:6px;font-size:28px;font-weight:700;line-height:1;margin-top:4px;color:#2b2b2b}

  .main-nav{position:absolute;left:405px;top:66px;height:68px;display:flex}
  .main-nav a{display:flex;align-items:center;height:68px;padding:0 14px;font-size:13px;font-weight:700;color:var(--nav-text);text-decoration:none;text-transform:uppercase;letter-spacing:.1px}
  .main-nav a+a{margin-left:5px}
  .main-nav a.is-active{color:var(--nav-active);background:#f3f3f3;border-bottom:6px solid var(--nav-active);height:74px;margin-bottom:-6px}

  .hero{position:absolute;left:0;top:134px;width:1200px;height:503px;
    background:
      radial-gradient(ellipse 320px 360px at 880px 300px,rgba(210,190,150,.55),transparent 70%),
      radial-gradient(ellipse 500px 300px at 600px 420px,rgba(230,220,120,.45),transparent 70%),
      linear-gradient(100deg,#8fa33a 0%,#5b7a1f 25%,#3f5a18 45%,#8c9a3c 60%,#4d6d1c 80%,#6f8a28 100%);}
  .hero-copy{position:absolute;left:149px;top:50px;color:var(--white);text-shadow:0 1px 3px rgba(0,0,0,.35)}
  .hero-title{font-size:42px;font-weight:300;letter-spacing:.5px;line-height:1}
  .hero-title b{font-weight:700}
  .hero-sub{font-size:24px;font-weight:600;margin-top:6px;display:flex;align-items:baseline;gap:8px}
  .hero-sub .price{font-size:42px;font-weight:700;color:var(--price-red);text-shadow:0 1px 2px rgba(255,255,255,.3)}
  .perks{list-style:none;margin-top:14px}
  .perks li{display:flex;align-items:center;gap:12px;height:33.5px;font-size:16px;font-weight:600}
  .perks svg{flex:none;margin-left:-3px}

  .cta-row{position:absolute;left:149px;top:376px;display:flex;align-items:center;gap:27px}
  .btn-start{display:flex;align-items:center;justify-content:center;gap:12px;width:247px;height:58px;border-radius:6px;background:linear-gradient(var(--btn-top),var(--btn-bottom));color:var(--white);font-size:28px;font-weight:700;text-decoration:none;text-shadow:0 1px 2px rgba(0,0,0,.25)}
  .badge{width:82px;height:72px;border-radius:50%;background:rgba(255,255,255,.9);border:3px solid var(--leaf)}
</style>
</head>
<body>
  <header class="site-header">
    <div class="brand">
      <span class="brand-mark"></span>
      <span class="brand-name">Tidy Nest</span>
    </div>
    <div class="call-box">
      <div class="call-line"><strong>Call Us</strong> to arrange your cleaning on</div>
      <div class="call-phone">
        <svg width="18" height="24" viewBox="0 0 18 24" aria-hidden="true"><path d="M5 1 L9 6 L6 9 Q8 15 12 18 L15 15 L18 19 L14 23 Q2 19 1 5 Z" fill="var(--brand-blue)"/></svg>
        555-214-0387
      </div>
    </div>
    <nav class="main-nav">
      <a class="is-active" href="#">Home</a>
      <a href="#">About Us</a>
      <a href="#">Our Services</a>
      <a href="#">Photos</a>
      <a href="#">Reviews</a>
      <a href="#">Tips</a>
      <a href="#">Careers</a>
      <a href="#">FAQ</a>
      <a href="#">Contact</a>
    </nav>
  </header>

  <section class="hero" role="img" aria-label="Photo: a woman in a green summer dress stretching her arms open on a sunlit forest path">
    <div class="hero-copy">
      <h1 class="hero-title">SIMPLIFY <b>YOUR LIFE</b></h1>
      <p class="hero-sub">and some there House Cleaning from <span class="price">$79</span></p>
      <ul class="perks">
        <li><svg width="24" height="28" viewBox="0 0 24 28"><path d="M2 26 Q0 8 22 2 Q24 22 2 26 Z" fill="var(--leaf)"/></svg>Locally Owned &amp; Operated</li>
        <li><svg width="24" height="28" viewBox="0 0 24 28"><path d="M2 26 Q0 8 22 2 Q24 22 2 26 Z" fill="var(--leaf)"/></svg>Reliable &amp; Affordable</li>
        <li><svg width="24" height="28" viewBox="0 0 24 28"><path d="M2 26 Q0 8 22 2 Q24 22 2 26 Z" fill="var(--leaf)"/></svg>All Supplies Provided</li>
        <li><svg width="24" height="28" viewBox="0 0 24 28"><path d="M2 26 Q0 8 22 2 Q24 22 2 26 Z" fill="var(--leaf)"/></svg>No Contracts</li>
        <li><svg width="24" height="28" viewBox="0 0 24 28"><path d="M2 26 Q0 8 22 2 Q24 22 2 26 Z" fill="var(--leaf)"/></svg>Pet Friendly</li>
        <li><svg width="24" height="28" viewBox="0 0 24 28"><path d="M2 26 Q0 8 22 2 Q24 22 2 26 Z" fill="var(--leaf)"/></svg>Green Cleaning</li>
      </ul>
    </div>
    <div class="cta-row">
      <a class="btn-start" href="#">GET STARTED
        <svg width="30" height="26" viewBox="0 0 30 26" aria-hidden="true"><path d="M0 8 H15 V0 L30 13 L15 26 V18 H0 Z" fill="var(--white)"/></svg>
      </a>
      <span class="badge" aria-hidden="true"></span>
    </div>
  </section>
</body>
</html>
```